Candle Rental Business seeks new website design

We need a new website design for a Candle hire business. The business rents out pillar candles for events such as weddings and corporate events. Our main target market is weddings. The business name is Hire a Lantern. The business name does not have a logo design.

We would like a website that is light in colours and creates a warm atmosphere. The design needs to be elegant and upmarket. There are different size candles that we hire out, ranging from 10cm diameter to 20cm diameter, flat, tall etc. All our candles are white in colour. Its just the size that differs.

We would also like to include a section for hiring out decor such as glassvases, candlebras, overlays and chairs sachets, chair covers. However, this is not the businesses main focus but an additional offering to customers.

Target Market(s)

Wedding venues and brides. Corporate events. School dances.

Industry/Entity Type

Hospitality

Logo Text

Hire a Lantern

Number of Pages Required

1 page

Font styles to use
Sans Serif
Script

Requirements
Must have
• Pictures of pillar candles. Plain white candles. The website must centre around candles.
Nice to have
• Different examples of candle centrepieces
Should not have
• Pictures must not be of brides. Pictures of surrounding is perferable.

```html
<!DOCTYPE html>
<html lang="en">
<head>
<meta charset="utf-8">
<title>Hire a Lantern – Candle Hire</title>
<link rel="stylesheet" href="https://fonts.googleapis.com/css2?family=Lobster+Two:ital,wght@1,700&family=Roboto+Slab:wght@600;700&family=Source+Sans+3:wght@400;600;700&display=swap">
<style>
:root{
  --pink:#f19ccb;
  --pink-dark:#e07fb4;
  --pink-text:#e0609f;
  --lilac-1:#c78ff3;
  --lilac-2:#b880e8;
  --lilac-3:#a874da;
  --purple:#9a5fd0;
  --grey-text:#8a8a8a;
  --body-text:#7a7a7a;
  --light-bg:#efefef;
  --footer:#343434;
  --white:#ffffff;
}
*{box-sizing:border-box;margin:0;padding:0}
html,body{width:1200px;height:3186px;overflow:hidden;background:var(--white)}
body{font-family:"Source Sans 3",Arial,sans-serif;color:var(--body-text);position:relative}
.slab{font-family:"Roboto Slab",Georgia,serif}

/* header */
.topbar{position:absolute;top:0;left:0;width:1200px;height:26px;background:var(--pink-dark);color:#fff;font-size:12px}
.topbar .contacts{position:absolute;right:96px;top:5px;display:flex;gap:22px}
.topbar .dot{display:inline-block;width:9px;height:9px;border-radius:50%;background:#fff;margin-right:6px;vertical-align:-1px}
.header{position:absolute;top:26px;left:0;width:1200px;height:76px;background:var(--pink)}
.brand{position:absolute;left:122px;top:16px;display:flex;align-items:center;gap:12px;color:#fff;font-family:"Roboto Slab",serif;font-weight:700;font-size:32px}
.brand .mark{width:40px;height:40px;background:#fff;border-radius:4px;opacity:.9}
.nav{position:absolute;left:486px;top:28px;display:flex;gap:30px;list-style:none}
.nav a{color:#fff;text-decoration:none;font-family:"Roboto Slab",serif;font-weight:700;font-size:13px;letter-spacing:.3px}
.nav .active{border-bottom:2px solid #fff;padding-bottom:6px}

/* hero */
.hero{position:absolute;top:102px;left:0;width:1200px;height:433px;
  background:radial-gradient(ellipse at 25% 30%,#f6e3c4 0%,transparent 30%),radial-gradient(ellipse at 80% 45%,#f5dfba 0%,transparent 28%),linear-gradient(180deg,#6b6c74 0%,#a49a90 45%,#d9cdc4 75%,#eee6e2 100%)}
.hero-badge{position:absolute;left:148px;top:67px;width:250px;height:250px;border-radius:50%;background:rgba(240,240,240,.95);text-align:center;padding-top:58px}
.hero-badge h1{font-family:"Lobster Two",cursive;font-style:italic;font-weight:700;font-size:36px;line-height:40px;color:var(--purple)}
.hero-badge p{margin-top:14px;font-family:"Roboto Slab",serif;font-weight:700;font-size:17px;line-height:24px;color:#7a7a7a}
.slide-arrow{position:absolute;top:216px;width:34px;height:34px;background:#333;display:flex;align-items:center;justify-content:center}
.slide-arrow.prev{left:10px}.slide-arrow.next{right:10px}

/* services */
.services{position:absolute;top:535px;left:0;width:1200px;height:287px;display:flex}
.service{flex:1;text-align:center;color:#fff;padding-top:28px}
.service:nth-child(1){background:var(--lilac-1)}
.service:nth-child(2){background:var(--lilac-2)}
.service:nth-child(3){background:var(--lilac-3)}
.service .icon{width:74px;height:86px;margin:0 auto;border-radius:8px;background:rgba(255,255,255,.35)}
.service h2{font-family:"Roboto Slab",serif;font-weight:700;font-size:29px;margin-top:14px}
.service p{font-size:13.5px;line-height:20px;margin:12px auto 0;width:320px}
.service .go{width:34px;height:34px;background:#fff;margin:14px auto 0;display:flex;align-items:center;justify-content:center}

/* section heading */
.sec-title{position:absolute;left:0;width:1200px;text-align:center;font-family:"Roboto Slab",serif;font-weight:700;font-size:32px;color:var(--grey-text)}
.sec-title em{font-style:normal;color:var(--pink-text)}
.sec-title::after{content:"";display:block;width:84px;height:2px;background:#bdbdbd;margin:14px auto 0}

/* welcome */
.welcome{position:absolute;top:822px;left:0;width:1200px;height:457px}
.welcome .photo{position:absolute;left:119px;top:121px;width:256px;height:256px;border-radius:50%;background:radial-gradient(circle at 50% 60%,#f3ebe0 0%,#c9c6bb 55%,#8f9289 100%)}
.welcome .copy{position:absolute;left:404px;top:126px;width:660px;font-size:14px;line-height:24px}
.welcome .lead{color:var(--pink-text);font-weight:600;font-size:15px}
.welcome .copy p{margin-bottom:14px}
.welcome .more{color:var(--purple);font-weight:700;font-size:12px}

/* decor */
.decor{position:absolute;top:1279px;left:0;width:1200px;height:654px;background:var(--light-bg)}
.decor .chart{position:absolute;left:186px;top:228px;width:300px;height:300px}
.decor .arc{position:absolute;left:116px;top:158px;width:440px;height:440px}
.decor-item{position:absolute;left:586px;display:flex;gap:20px;width:520px}
.decor-item .ic{width:74px;height:74px;border-radius:50%;background:#fff;border:5px solid #ddd;flex:none;display:flex;align-items:center;justify-content:center}
.decor-item .ic span{width:32px;height:32px;border-radius:50%;background:#8f8f8f}
.decor-item h3{font-family:"Roboto Slab",serif;font-size:18px;color:var(--pink-text);margin-top:2px}
.decor-item p{font-size:13.5px;line-height:21px;margin-top:6px}

/* promo */
.promo{position:absolute;top:1933px;left:0;width:1200px;height:484px;
  background:radial-gradient(ellipse at 22% 65%,#f1e6ef 0%,#c3a2c3 22%,transparent 45%),linear-gradient(90deg,#5b3757 0%,#7a3f86 40%,#8a48a8 70%,#7c3d99 100%)}
.promo .copy{position:absolute;left:529px;top:92px;color:#fff;font-family:"Roboto Slab",serif;font-weight:600;font-size:21px;line-height:32px}
.promo .copy .big{font-weight:700;font-size:23px}
.promo .copy p{margin-bottom:20px}
.buy{position:absolute;left:529px;top:297px;width:110px;height:110px;border-radius:50%;background:#b37be4;color:#fff;text-align:center;font-family:"Roboto Slab",serif;font-weight:700;font-size:16px;padding-top:36px}

/* testimonials */
.testimonials{position:absolute;top:2417px;left:0;width:1200px;height:338px}
.avatar{position:absolute;left:149px;top:143px;width:116px;height:116px;border-radius:50%;border:4px solid #eee;background:linear-gradient(160deg,#d8cbc2,#9b8f88)}
.who{position:absolute;left:291px;top:178px}
.who h4{font-family:"Roboto Slab",serif;font-size:18px;color:var(--purple)}
.who span{font-size:13px}
.pointer{position:absolute;left:410px;top:148px}
.quote{position:absolute;left:484px;top:152px;width:600px;font-size:14px;line-height:24px;color:var(--purple)}
.quote::before{content:"\201C";font-family:Georgia,serif;font-size:30px;color:#c6a6e8;margin-right:4px;vertical-align:-8px}
.dots{position:absolute;top:290px;left:553px;display:flex;gap:12px}
.dots span{width:12px;height:12px;border-radius:50%;border:1px solid #aaa}
.dots .on{background:#aaa}
.testimonials .rule{position:absolute;left:120px;top:264px;width:960px;height:1px;background:#eee}

/* partners */
.partners{position:absolute;top:2755px;left:0;width:1200px;height:130px;background:var(--light-bg);display:flex;justify-content:center;align-items:center;gap:46px}
.partners span{width:118px;height:34px;border-radius:4px;background:#d9d9d9}

/* footer */
.footer-edge{position:absolute;top:2885px;left:0;width:1200px;height:10px;background:linear-gradient(90deg,var(--pink),#b990e6,var(--pink))}
.footer{position:absolute;top:2895px;left:0;width:1200px;height:291px;background:var(--footer);color:#ddd;font-size:12.5px}
.fcol{position:absolute;top:38px}
.fcol h5{font-size:13px;font-weight:700;color:#fff;letter-spacing:.4px;margin-bottom:14px}
.fcol ul{list-style:none;line-height:23px}
.fcol li::before{content:"›";margin-right:8px}
.field{width:172px;height:30px;background:#fff;color:#999;font-size:11px;padding:8px 10px;margin:12px 0 12px}
.btn{display:inline-block;background:var(--lilac-2);color:#fff;font-size:11px;font-weight:700;padding:5px 14px}
.news{display:flex;gap:10px;margin-bottom:16px}
.news .sq{width:10px;height:10px;border:1px solid #ddd;margin-top:4px;flex:none}
.news b{color:#fff}
.fbrand{font-family:"Roboto Slab",serif;font-weight:700;font-size:19px;color:#fff;display:flex;gap:8px;align-items:center;margin-bottom:6px}
.fbrand i{width:22px;height:22px;background:#fff;display:block}
.phone{display:flex;align-items:center;gap:12px;color:#fff;font-weight:700;margin-top:8px}
.copyright{position:absolute;left:161px;top:255px;font-size:12px}
.social{position:absolute;right:134px;top:250px;display:flex;gap:6px}
.social span{width:22px;height:22px;background:#fff;border-radius:3px}
.social span:first-child{background:var(--lilac-2)}
</style>
</head>
<body>

<div class="topbar"><div class="contacts"><span><i class="dot"></i>555-014-2290</span><span><i class="dot"></i>info@hirealantern.example</span></div></div>
<header class="header">
  <div class="brand"><span class="mark"></span>Hire A Lantern</div>
  <ul class="nav">
    <li><a class="active" href="#">HOME</a></li><li><a href="#">ABOUT US</a></li><li><a href="#">OUR PRODUCTS</a></li><li><a href="#">HIRE CANDLES</a></li><li><a href="#">DÉCOR HIRE</a></li><li><a href="#">CONTACT US</a></li>
  </ul>
</header>

<section class="hero" role="img" aria-label="Photo of a reception table set with white pillar candles in glass holders and soft bokeh lights">
  <div class="hero-badge"><h1>Decorative<br>Candles</h1><p>Creating A Warm<br>Atmosphere &amp; Special<br>Touch To All<br>Occasions.</p></div>
  <div class="slide-arrow prev"><svg width="12" height="14"><path d="M9 1 3 7l6 6" stroke="#fff" stroke-width="2" fill="none"/></svg></div>
  <div class="slide-arrow next"><svg width="12" height="14"><path d="M3 1l6 6-6 6" stroke="#fff" stroke-width="2" fill="none"/></svg></div>
</section>

<section class="services">
  <div class="service"><div class="icon" role="img" aria-label="Candle icon"></div><h2>Hire Candles</h2><p>Lorem ipsum dolor sit amet, consectetuer adipiscing elit, sed diam nonummy nibh euismod tincidunt</p><div class="go"><svg width="10" height="14"><path d="M2 1l6 6-6 6" stroke="#999" stroke-width="2" fill="none"/></svg></div></div>
  <div class="service"><div class="icon" role="img" aria-label="Pair of candles icon"></div><h2>Personalised Candles</h2><p>Lorem ipsum dolor sit amet, consectetuer adipiscing elit, sed diam nonummy nibh euismod tincidunt</p><div class="go"><svg width="10" height="14"><path d="M2 1l6 6-6 6" stroke="#999" stroke-width="2" fill="none"/></svg></div></div>
  <div class="service"><div class="icon" role="img" aria-label="Candelabra icon"></div><h2>Décor Hire</h2><p>Lorem ipsum dolor sit amet, consectetuer adipiscing elit, sed diam nonummy nibh euismod tincidunt</p><div class="go"><svg width="10" height="14"><path d="M2 1l6 6-6 6" stroke="#999" stroke-width="2" fill="none"/></svg></div></div>
</section>

<section class="welcome">
  <h2 class="sec-title" style="top:44px">Welcome To <em>Hire A Lantern</em></h2>
  <div class="photo" role="img" aria-label="Photo of white pillar candles with a white flower centrepiece"></div>
  <div class="copy">
    <p class="lead">Candles Create A Warm Atmosphere And Special Touch To All Occasions.It Is Much Cheaper Renting Than Buying Candles For Your Event.</p>
    <p>We DESIGN, MANUFACTURE, and PERSONALISE all of our CANDLES in our most distinctive handcrafted manner! Whether you are looking for candles for a wedding, birthday, anniversary, engagement, graduation, bridal or baby showers, baby christening, retirement, or any special occasion candles you can order it from us.</p>
    <p>We are a family owned and operated company and began making decorative candles for all occasions. All of our candles are individually hand made in our candle studio, situated in Harbourvale, outside Eastmere. Our wax is local and of a very high quality, and dripless! Our wax is also made with a high melting point, which means it will not melt or bend in hot temperatures.</p>
    <span class="more">READ MORE</span>
  </div>
</section>

<section class="decor">
  <h2 class="sec-title" style="top:52px">Our <em>Hiring Out Decor</em></h2>
  <svg class="arc" viewBox="0 0 440 440">
    <path d="M329 64A190 190 0 0 1 329 376" fill="none" stroke="#9a5fd0" stroke-width="5"/>
    <g stroke="#cfcfcf" stroke-width="1.5"><line x1="402" y1="146" x2="474" y2="97"/><line x1="410" y1="178" x2="474" y2="180"/></g>
    <circle cx="395" cy="151" r="7" fill="#e07fb4" stroke="#fff" stroke-width="2"/>
    <circle cx="410" cy="218" r="7" fill="#e07fb4" stroke="#fff" stroke-width="2"/>
    <circle cx="395" cy="289" r="7" fill="#e07fb4" stroke="#fff" stroke-width="2"/>
  </svg>
  <svg class="chart" viewBox="0 0 300 300" role="img" aria-label="Ring chart of decor categories">
    <g stroke="#efefef" stroke-width="3">
      <path d="M12 150A138 138 0 0 1 150 12L150 80A70 70 0 0 0 80 150Z" fill="#eaa6cb"/>
      <path d="M150 12A138 138 0 0 1 288 150L220 150A70 70 0 0 0 150 80Z" fill="#d774ab"/>
      <path d="M288 150A138 138 0 0 1 150 288L150 220A70 70 0 0 0 220 150Z" fill="#f07cb7"/>
      <path d="M150 288A138 138 0 0 1 12 150L80 150A70 70 0 0 0 150 220Z" fill="#f596c6"/>
    </g>
    <circle cx="150" cy="150" r="64" fill="#fff"/>
    <circle cx="150" cy="150" r="54" fill="#9a5fd0"/>
    <rect x="138" y="132" width="24" height="34" rx="3" fill="#fff" opacity=".85"/>
    <g fill="#fff" font-family="Source Sans 3,sans-serif" font-size="14" text-anchor="middle">
      <text transform="translate(80 84) rotate(-45)">Glass Vases</text>
      <text transform="translate(222 84) rotate(45)">Candle Bars</text>
      <text transform="translate(222 226) rotate(-45)">Chair Sachets</text>
      <text transform="translate(80 226) rotate(45)">Chair Covers</text>
    </g>
  </svg>
  <div class="decor-item" style="top:155px"><div class="ic"><span></span></div><div><h3>Glass Vases</h3><p>Lorem ipsum dolor sit amet, consectetuer adipiscing elit,<br>sed diam nonummy nibh euismod tincidunt ut laoreet</p></div></div>
  <div class="decor-item" style="top:282px"><div class="ic"><span></span></div><div><h3>Candle Bars</h3><p>Lorem ipsum dolor sit amet, consectetuer adipiscing elit,<br>sed diam nonummy nibh euismod tincidunt ut laoreet</p></div></div>
  <div class="decor-item" style="top:414px"><div class="ic"><span></span></div><div><h3>Overlays &amp; Chair Sachets</h3><p>Lorem ipsum dolor sit amet, consectetuer adipiscing elit,<br>sed diam nonummy nibh euismod tincidunt ut laoreet</p></div></div>
  <div class="decor-item" style="top:541px"><div class="ic"><span></span></div><div><h3>Chair Covers</h3><p>Lorem ipsum dolor sit amet, consectetuer adipiscing elit,<br>sed diam nonummy nibh euismod tincidunt ut laoreet</p></div></div>
</section>

<section class="promo" role="img" aria-label="Photo of two white pillar candles with festive ornaments on a purple blurred background">
  <div class="copy">
    <p><span class="big">We DESIGN, MANUFACTURE &amp; PERSONALISE</span><br>All Of Our CANDLES In Our Most Distinctive<br>Handcrafted Manner!</p>
    <p>Different Size Candles Ranging From<br>10cm Diameter To 20cm Diameter, Flat, Tall Etc</p>
  </div>
  <div class="buy">BUY NOW<br><svg width="18" height="14"><path d="M2 2l5 5-5 5M9 2l5 5-5 5" stroke="#fff" stroke-width="2" fill="none"/></svg></div>
</section>

<section class="testimonials">
  <h2 class="sec-title" style="top:50px">What Our <em>Clients Say</em></h2>
  <div class="avatar" role="img" aria-label="Client portrait"></div>
  <div class="who"><h4>Clara Whitford</h4><span>Home Maker</span></div>
  <svg class="pointer" width="40" height="110"><path d="M1 1 38 55 1 109" fill="none" stroke="#e3e3e3" stroke-width="2"/></svg>
  <p class="quote">Lorem ipsum dolor sit amet, consectetuer adipiscing elit, sed diam nonummy nibh euismod tincidunt ut laoreet dolore magna aliquam erat volutpat. Ut wisi enim ad minim veniam, quis nostrud exerci tation ullamcorper suscipit lobortis nisl ut aliquip ex ea commodo consequat.</p>
  <div class="rule"></div>
  <div class="dots"><span></span><span class="on"></span><span></span><span></span></div>
</section>

<section class="partners"><span></span><span></span><span></span><span></span><span></span><span></span></section>

<div class="footer-edge"></div>
<footer class="footer">
  <div class="fcol" style="left:161px"><h5>QUICK LINK</h5><ul><li>Home</li><li>About Us</li><li>Our Products</li><li>Hire Candles</li><li>Décor Hire</li><li>Contact Us</li></ul></div>
  <div class="fcol" style="left:325px;width:190px"><h5>NEWSLETTER SIGN UP</h5><p>Lorem ipsum dolor sit amet lorem adipiscing elit amet</p><div class="field">Email Address</div><span class="btn">SUBSCRIBE</span></div>
  <div class="fcol" style="left:595px;width:210px"><h5>LATEST NEWS</h5>
    <div class="news"><i class="sq"></i><div><b>Lorem ipsum dolor sit amet</b><br>Lorem ipsum dolor sit amet, cons ectetuer adipiscing elit</div></div>
    <div class="news"><i class="sq"></i><div><b>Lorem ipsum dolor sit amet</b><br>Lorem ipsum dolor sit amet, cons ectetuer adipiscing elit</div></div>
  </div>
  <div class="fcol" style="left:856px;width:200px"><h5>GET IN TOUCH</h5>
    <div class="fbrand"><i></i>Hire A Lantern</div>
    <p>Lorem ipsum dolor sit amet, cons ectetuer adipiscing elit</p>
    <div class="phone"><svg width="12" height="12"><path d="M2 1h3l1 3-2 1a7 7 0 0 0 3 3l1-2 3 1v3c-6 0-9-3-9-9z" fill="#fff"/></svg>555-014-2290</div>
    <div class="phone"><svg width="12" height="12"><rect x="1" y="4" width="10" height="6" fill="#fff"/><rect x="3" y="1" width="6" height="3" fill="#fff"/></svg>555-014-2291</div>
  </div>
  <p class="copyright">Copyright © 2016 HIRE A LANTERN | All Rights Reserved.</p>
  <div class="social"><span></span><span></span><span></span><span></span></div>
</footer>

</body>
</html>
```